Supplement Brand Product Labels

Product Label for Supplement Brand

Protein Powder Label (2 x different flavours)

Neon Colours / Skull / Spooky
Refer to pictures below, they are the look we are wanting to go with but put our touch to it aswell.

Target Market(s)

Fitness

Industry/Entity Type

Supplement Brand

Colors
0054AA
0677BA
7BADD7
CADEEF
E8F1F8
0094D4
00A9DD
6FCCEA
C7EBF8
E9F6FB
00AB8E
00BBA5
67D7C9
C6EFE9
E9F9F6
59FF00
82FF00
B8FF75
E3FFCB
F4FFEA
FFF300
FFF600
FEFA6F
FFFEC7
FFFEE8
FFC000
F8CF3A
FAE287
FDF2CF
FEFAEE
F0912C
F2A743
F7CA91
FBE8D2
FDF5EE
EE7325
F08F49
F5BC92
FAE3D3
FDF4ED
EB3D1F
EC4F4E
F09395
F8D3D4
FCEDEE
E54698
E96AAD
F1A4CE
F9D9EA
FCEFF6
A7469A
B969AE
D3A5CF
EDDBEB
F8F0F9
6B429C
8869AF
B7A5CE
E3DAEB
F3F0F8

Requirements
Nice to have
• Skull, Neon Colours, Abstract, Barbell, Lighting Bolt, Flames, Spooky

```html
<!DOCTYPE html>
<html lang="en">
<head>
<meta charset="utf-8">
<title>Grimforge Supps – BCAA 2:1:1 Label</title>
<link href="https://fonts.googleapis.com/css2?family=Anton&family=Archivo+Black&family=Roboto+Condensed:wght@400;600;700&family=Rubik:wght@600;700&display=swap" rel="stylesheet">
<style>
  :root{
    --page:#ffffff;
    --label:#000000;
    --ink:#ffffff;
    --neon:#59ff00;
    --neon-soft:#82ff00;
    --glow-deep:#0b3a12;
    --glow-mid:#1f9a2a;
    --table-ink:#1a1a1a;
  }
  *{box-sizing:border-box;margin:0;padding:0}
  html,body{width:1200px;height:1200px;overflow:hidden;background:var(--page)}
  body{position:relative;font-family:"Roboto Condensed",sans-serif}

  .label{
    position:absolute;left:30px;top:370px;width:1140px;height:461px;
    background:var(--label);color:var(--ink);overflow:hidden;
  }

  /* left panel */
  .directions{position:absolute;left:56px;top:24px;width:306px}
  .section-title{
    font-family:"Rubik",sans-serif;font-weight:700;color:var(--neon);
    font-size:16px;letter-spacing:-.3px;margin-bottom:10px;
  }
  .directions p{font-size:11px;font-weight:600;line-height:16.5px;margin-bottom:16px;text-align:justify}
  .directions p.mix{text-align:left}

  .brand-small{position:absolute;left:56px;top:312px}
  .brand-small .name{
    font-family:"Anton",sans-serif;font-size:30px;line-height:1;color:var(--ink);letter-spacing:.5px;
  }
  .brand-small .name span{display:block;font-size:15px;letter-spacing:3px;margin-top:2px}
  .website{position:absolute;left:56px;top:405px;font-size:11px;font-weight:700}

  /* centre panel */
  .hero-art{
    position:absolute;left:400px;top:0;width:360px;height:461px;
    background:radial-gradient(ellipse 55% 50% at 50% 52%, var(--glow-mid) 0%, var(--glow-deep) 45%, var(--label) 80%);
  }
  .brand-hero{
    position:absolute;left:400px;top:18px;width:360px;text-align:center;
    font-family:"Anton",sans-serif;color:var(--ink);line-height:1;
  }
  .brand-hero .name{font-size:54px;letter-spacing:1px}
  .brand-hero .name span{display:block;font-size:26px;letter-spacing:6px;margin-top:2px}
  .product-name{
    position:absolute;left:400px;top:372px;width:360px;text-align:center;
    font-family:"Anton",sans-serif;font-size:52px;line-height:1;letter-spacing:2px;
  }
  .product-name .ratio{color:var(--neon)}

  /* right panel */
  .nutrition{
    position:absolute;left:826px;top:27px;width:296px;height:259px;
    background:#fff;border:2px solid #fff;outline:1px solid #555;outline-offset:-4px;
    color:var(--table-ink);font-family:"Rubik",sans-serif;
  }
  .nutrition table{width:100%;border-collapse:collapse}
  .nutrition th{
    font-size:9.5px;font-weight:600;line-height:11px;text-align:center;vertical-align:bottom;
    padding:8px 4px 6px;border-bottom:1.5px solid #333;
  }
  .nutrition th:first-child{text-align:left;padding-left:8px}
  .nutrition td{font-size:11px;font-weight:400;height:29.6px;text-align:center;padding:0 4px}
  .nutrition td:first-child{text-align:left;padding-left:8px;white-space:nowrap}

  .ingredients{position:absolute;left:832px;top:304px}
  .ingredients .section-title{font-size:17px;margin-bottom:6px;letter-spacing:.5px}
  .ingredients p{font-size:11px;font-weight:700;letter-spacing:-.3px}

  .origin{position:absolute;left:870px;top:398px;display:flex;align-items:center;gap:6px}
  .origin svg{display:block}
  .origin .text{font-family:"Archivo Black",sans-serif;font-size:15px;line-height:14px;letter-spacing:.5px}
</style>
</head>
<body>
<section class="label">

  <div class="directions">
    <h2 class="section-title">Directions Of Use</h2>
    <p class="mix">Mix 7g (1 scoop) with 250ml's of cold water/ juice.</p>
    <p>Formulated supplementary sports food. Not suitable for children under 15 years of age or pregnant women. Should only be used under medical or dietetic supervision. This product is not a sole source of nutrition and should be consumed in conjunction with a nutritious diet and appropriate physical training or exercise program.</p>
    <p class="mix">Store in a cool dry place out of direct sunlight.</p>
  </div>

  <div class="brand-small"><div class="name">GRIMFORGE<span>SUPPS</span></div></div>
  <div class="website">www.grimforgesupps.com</div>

  <div class="hero-art" role="img" aria-label="Illustration of a skull wreathed in glowing neon green flames"></div>
  <div class="brand-hero"><div class="name">GRIMFORGE<span>SUPPS</span></div></div>
  <div class="product-name">BCAA <span class="ratio">2:1:1</span></div>

  <div class="nutrition">
    <table>
      <thead>
        <tr>
          <th>35.7 Servings<br>Per 250g Packet<br>7 Grams Per Serve</th>
          <th>Average Quantity<br>Per Serving</th>
          <th>Average Quantity<br>Per 100g</th>
        </tr>
      </thead>
      <tbody>
        <tr><td>Energy (KJ)</td><td>119</td><td>1700</td></tr>
        <tr><td>Protein (G)</td><td>7</td><td>100</td></tr>
        <tr><td>Total Carbohydrates (G)</td><td>0</td><td>0</td></tr>
        <tr><td>(Sugar) (G)</td><td>0</td><td>0</td></tr>
        <tr><td>Total Fats (G)</td><td>0</td><td>0</td></tr>
        <tr><td>Sodium (MG)</td><td>0</td><td>0</td></tr>
        <tr><td>BCAA 2:1:1 (G)</td><td>7</td><td>100</td></tr>
      </tbody>
    </table>
  </div>

  <div class="ingredients">
    <h2 class="section-title">Ingredients</h2>
    <p>Arginine Alpha-Ketoglutarate</p>
  </div>

  <div class="origin">
    <svg width="34" height="28" viewBox="0 0 34 28" aria-hidden="true"><rect x="2" y="2" width="30" height="24" rx="4" fill="var(--neon)"/></svg>
    <div class="text">MADE IN<br>AUSTRALIA</div>
  </div>

</section>
</body>
</html>
```